Garlic Farm for Farm Sales/Restaurant sales

Need a professional, but appealing to agriculture world. We are selling 27 kinds of Organic Garlic from a farm in Simla,CO. I have uploaded logo and business information-we are going to need a template, because I will need to use it for four separate people.
-We are trying to appeal to Farm to table restaurants
-As well as growers/farmers

Target Market(s)

Agriculture Sales/Restaurants-Organic

Industry/Entity Type

Agriculture

Contact Information for Business Card

Want it to look more unique then your average kelto stock card- I want it to look amazing

Font styles to use
Sans Serif

Colors
0455a3
ec1f27
fbed22
ffffff

Requirements
Must have
• Just be creative
Nice to have
• Colorful
Should not have
• plain

```html
<!DOCTYPE html>
<html lang="en">
<head>
<meta charset="utf-8">
<title>Plains Crest Garlic – Business Card</title>
<link rel="stylesheet" href="https://fonts.googleapis.com/css2?family=Source+Sans+3:ital,wght@0,400;0,600;0,700;1,600&display=swap">
<style>
  :root {
    --stage-top: #2f2f2f;
    --stage-bottom: #222222;
    --card-front: #f2d306;
    --card-back: #fddb02;
    --brand-red: #c8102e;
    --brand-navy: #13306b;
    --ink: #1a1a1a;
  }
  * { margin: 0; padding: 0; box-sizing: border-box; }
  html, body { width: 1200px; height: 900px; overflow: hidden; }
  body {
    background: linear-gradient(180deg, var(--stage-top), var(--stage-bottom));
    font-family: "Source Sans 3", "Myriad Pro", Arial, sans-serif;
    position: relative;
  }
  .card {
    position: absolute;
    top: 300px;
    width: 442px;
    height: 273px;
    border-radius: 12px;
  }
  .card--front { left: 152px; background: var(--card-front); }
  .card--back { left: 622px; background: var(--card-back); }

  .front-mark {
    position: absolute;
    left: 52px;
    top: 64px;
    width: 130px;
    display: flex;
    flex-direction: column;
    align-items: center;
    gap: 8px;
  }
  .mark-dot {
    width: 104px; height: 104px;
    border-radius: 50%;
    background: var(--brand-red);
  }
  .brand-name {
    color: var(--brand-navy);
    font-weight: 700;
    font-size: 15px;
    white-space: nowrap;
  }

  .contact {
    position: absolute;
    left: 224px;
    top: 52px;
    color: var(--ink);
    font-size: 13px;
    line-height: 16px;
  }
  .contact__name {
    color: var(--brand-red);
    font-style: italic;
    font-weight: 600;
    font-size: 24px;
    line-height: 28px;
  }
  .contact__role { font-size: 16px; line-height: 18px; margin-bottom: 16px; }
  .contact__label { color: var(--brand-red); font-weight: 600; }
  .contact__web { color: var(--brand-red); }
  .contact__address { margin-top: 16px; }

  .back-mark {
    position: absolute;
    inset: 0;
    display: flex;
    flex-direction: column;
    align-items: center;
    justify-content: center;
    gap: 10px;
    padding-bottom: 8px;
  }
  .back-mark .mark-dot { width: 80px; height: 80px; }
  .back-mark .brand-name { font-size: 30px; }
</style>
</head>
<body>
  <section class="card card--front" aria-label="Business card front">
    <div class="front-mark">
      <span class="mark-dot"></span>
      <span class="brand-name">Plains Crest Garlic</span>
    </div>
    <div class="contact">
      <p class="contact__name">Dana Whitfield</p>
      <p class="contact__role">Owner</p>
      <p><span class="contact__label">P:</span> 719-555-0142</p>
      <p><span class="contact__label">F:</span> (719) 555-0187</p>
      <p><span class="contact__label">E:</span> hello@plainscrest.farm</p>
      <p class="contact__web">www.plainscrest.farm</p>
      <p class="contact__address">PO Box 2180,<br>Simla, CO 80835</p>
    </div>
  </section>

  <section class="card card--back" aria-label="Business card back">
    <div class="back-mark">
      <span class="mark-dot"></span>
      <span class="brand-name">Plains Crest Garlic</span>
    </div>
  </section>
</body>
</html>
```